Letterhead for Business Law Firm

We need a letter head for our firm based on the design we have settled on and it is attached. Our clients are small and large businesses around the world, and our letterhead is used typically for formal legal purposes such as demand letters (accusing the recipient of doing bad things) or responding to demand letters. It may also be sent to regulators and other government agencies. So this needs to be tasteful, but a little edgy as well - we try to convey that we are a firm that is different - businesses and investors come to us for creative, quick advice, typically in high stress circumstances, and for our ability to work through high conflict situations, and rapid paced engagements.

Target Market(s)

Lawyers, business executives, investors, government regulators who may receive letters from this firm on behalf of its clients.

Industry/Entity Type

Business

Requirements
Must have
• The design and the firm's contact information:
• Thornwell Law Firm, P.C.
• 1876 NE 57th Ave
• Portland, OR 97213
• phone: 971 555 0147
• fax: 971 555 0182
• in what placement and how depicted (e.g. a phone icon instead of the word "phone") I leave to your creative ideas.
Nice to have
• design and information can be placed at the top, bottom and/or sides of the letter, and the design should be for a standard letter size paper - and can have a separate design for the second page.

```html
<!DOCTYPE html>
<html lang="en">
<head>
<meta charset="utf-8">
<title>Thornwell Law Firm, P.C. — Letterhead</title>
<link rel="stylesheet" href="https://fonts.googleapis.com/css2?family=Source+Sans+3:wght@400&display=swap">
<style>
  :root {
    --teal: #3f7378;
    --ink: #231f20;
    --text: #4a4a4a;
    --rule: #9a9a9a;
    --paper: #ffffff;
    --backdrop: #ececec;
  }
  * { margin: 0; padding: 0; box-sizing: border-box; }
  html, body {
    width: 1019px;
    height: 1200px;
    overflow: hidden;
    background: var(--backdrop);
  }
  .letterhead {
    position: relative;
    width: 1019px;
    height: 1200px;
    background: var(--paper);
    font-family: "Source Sans 3", "Myriad Pro", Arial, sans-serif;
    font-weight: 400;
    color: var(--text);
  }
  .decor {
    position: absolute;
    inset: 0;
    width: 1019px;
    height: 1200px;
  }
  .brand {
    position: absolute;
    left: 75px;
    top: 58px;
    display: flex;
    align-items: center;
    gap: 16px;
  }
  .brand-mark {
    width: 76px;
    height: 76px;
    background: var(--teal);
    flex: none;
  }
  .brand-name {
    display: flex;
    flex-direction: column;
    color: var(--ink);
    line-height: 1;
  }
  .brand-name .firm {
    font-size: 40px;
    letter-spacing: 9px;
  }
  .brand-name .entity {
    margin-top: 8px;
    font-size: 17px;
    letter-spacing: 6.2px;
  }
  .contact {
    position: absolute;
    left: 807px;
    top: 53px;
    height: 83px;
    border-left: 1px solid var(--rule);
    padding-left: 14px;
    padding-top: 3px;
    list-style: none;
    font-size: 14.5px;
    line-height: 19.5px;
    white-space: nowrap;
  }
  .contact li {
    display: flex;
    align-items: center;
    gap: 5px;
  }
  .contact svg {
    width: 11px;
    height: 11px;
    flex: none;
  }
  .address {
    position: absolute;
    right: 53px;
    top: 1128px;
    text-align: right;
    color: var(--paper);
    font-size: 15.5px;
    line-height: 23px;
    font-style: normal;
    white-space: nowrap;
  }
</style>
</head>
<body>
<main class="letterhead">
  <svg class="decor" viewBox="0 0 1019 1200" aria-hidden="true">
    <path d="M0,0 H174 C95,10 28,52 0,109 Z" fill="var(--teal)"/>
    <path d="M10,96 C42,42 100,12 152,3 C104,20 55,50 10,96 Z" fill="var(--ink)"/>
    <path d="M3,114 C40,48 110,10 178,2" fill="none" stroke="var(--teal)" stroke-width="2"/>

    <path d="M1019,1088 C860,1108 700,1150 540,1174 C400,1194 200,1192 0,1184 V1200 H1019 Z" fill="var(--teal)"/>
    <path d="M0,1130 C40,1160 120,1174 250,1179 C380,1183 480,1177 560,1166 C450,1186 250,1192 0,1176 Z" fill="var(--ink)"/>
    <path d="M0,1182 C200,1193 400,1190 560,1171" fill="none" stroke="var(--paper)" stroke-width="3"/>
    <path d="M94,1162 C300,1174 600,1164 800,1122 C900,1102 960,1091 1019,1083" fill="none" stroke="var(--teal)" stroke-width="2"/>
  </svg>

  <div class="brand">
    <span class="brand-mark"></span>
    <span class="brand-name">
      <span class="firm">THORNWELL</span>
      <span class="entity">LAW FIRM, P.C.</span>
    </span>
  </div>

  <ul class="contact">
    <li>
      <svg viewBox="0 0 10 10" aria-label="Phone"><circle cx="5" cy="5" r="4.3" fill="none" stroke="var(--teal)" stroke-width="1"/><path d="M3.4,2.6 L4.4,2.4 L4.8,3.8 L4.1,4.3 C4.4,5 5,5.6 5.7,5.9 L6.2,5.2 L7.6,5.6 L7.4,6.6 C5.4,6.8 3.2,4.6 3.4,2.6 Z" fill="var(--teal)"/></svg>
      971 555 0147
    </li>
    <li>
      <svg viewBox="0 0 10 10" aria-label="Fax"><rect x="3" y="1" width="4" height="3" fill="var(--teal)"/><rect x="1" y="4" width="8" height="4" rx="1" fill="var(--teal)"/><rect x="2.5" y="7" width="5" height="2.5" fill="var(--teal)"/></svg>
      971 555 0182
    </li>
    <li>
      <svg viewBox="0 0 10 10" aria-label="Email"><rect x="0.8" y="2.5" width="8.4" height="5.5" fill="var(--teal)"/><path d="M0.8,2.5 L5,5.6 L9.2,2.5" fill="none" stroke="#fff" stroke-width="0.9"/></svg>
      info@thornwell.com
    </li>
    <li>
      <svg viewBox="0 0 10 10" aria-label="Website"><circle cx="5" cy="5" r="4.2" fill="none" stroke="var(--teal)" stroke-width="1"/><ellipse cx="5" cy="5" rx="1.8" ry="4.2" fill="none" stroke="var(--teal)" stroke-width="0.8"/><path d="M0.8,5 H9.2" stroke="var(--teal)" stroke-width="0.8"/></svg>
      www.thornwell.com
    </li>
  </ul>

  <address class="address">
    1876 NE 57th Ave<br>
    Portland, OR 97213
  </address>
</main>
</body>
</html>
```